Online Psychiatry business - Business Card

I need a business card design. The target audience is busy professionals of any field (this therapy appeals best to 24-35 year olds). It involves psychiatry by tele-medicine (or video-conference). Nothing on it should be a giveaway that it's about mental health. Professional design with silver or gold as the primary colors appeals to me. The card must be as simple and as uncluttered as possible. Some color and flowing design on the edge of the card appeals to me.
CalmHarborDirect.net should probably appear in the center of the card and stand out, i.e. bold lettering, and easy to read, no cursive, but Ariel Black. Some where below this, should appear "Too Busy to Take Care of Yourself? Think again." Since this isn't office based, I don't think an office address is necessary and limits clutter.
Information that does need to appear is my name: Gerald Mossvane, MD
General phone number: 555-417-8062. I'm hoping to get an 24-hour answering service soon so leave a little room for this. In addition I want to include two email addresses:
CalmHarborDirect@mailbox-example.net and CalmHarbor247@mailbox-example.net
Updates

I like the designs. I would like someone to put the website in bold in the center

 as most have been doing with a smaller font reminder nearby saying "No time" etc.
but I'd like to put my name down in the corner with the rest of the contact material.
Black print against a white or grey background appeals to me, with darker silver artwork near the sides (simple abstract, like wavy lines or something you can one up with that works. 
thanks

I ve tried to provide as much feedback as possible given my time limits, so if you have extra questions, please feel free to email. I tried to attach a file of a business card I really like but make be difficult to actually manufacture. I'm going to send you a link to the photo. The card has a pull tab. There is not much information on the outside. In fact, if you were to design the outside, I would just print : Too Busy to Take Care of Yourself? Think Again.

When you pull the tab the remaining information is on the bottom half of the card. Please don't use the color pink!!!!
http://www.cardgallery-example.org/2009/05/100-clever-print-ideas/
It is the 39th photo on the list, about 2/3ds of the way down the page. It is titled: Faltenkiste

#7 and #16 have an appeal to me, except for the dot patterns
Hope this helps

I'm running out of time and energy. I 've been trying to give do down the list and give  individual feedback but I won't be able to do that anymore.

So if you have any specific questions, write me, and again thank you for all your effort!!

I know i received your files, including your zip files, Pindrel,

but Milo, did you send me the files including ZIP on project 6143907?
thanks

Target Market(s)

Working professionals and executive, attorneys, etc.

Industry/Entity Type

Business

Logo Text

Don't Have Time to Take Care of Yourself? Think Again.

Logo styles of interest
Pictorial/Combination Logo
Wordmark Logo
Font styles to use
Other font styles liked:
• Ariel Black appeals to me the most

Requirements
Must have
• Want to emphasize that the website must be obvious, easily found (The CalmHarborDirect.net)
For that reason i'd like the card to be white, and minimal decoration on one or both sides just to add some style and color
Nice to have
• A Very uncluttered, elegant design, and something that makes it stick in your head-doesn't everyone want the last?
Should not have
• Nothing on the card that give it away that this is about psychiatry, such as brain or other symbol, but also nothing that gives it away as a medical business, such as a stethoscope or red cross or anything.

```html
<!DOCTYPE html>
<html lang="en">
<head>
<meta charset="utf-8">
<title>CalmHarborDirect.net – Business Card</title>
<link href="https://fonts.googleapis.com/css2?family=Arimo:wght@700&family=Source+Sans+3:wght@400;600&display=swap" rel="stylesheet">
<style>
  :root {
    --backdrop: #e9e6e1;
    --ink-dark: #3a3a3a;
    --band-dark: #3b3b3b;
    --gold: #d9b437;
    --gold-text: #caa22a;
    --gold-light: #f6ec8a;
    --gold-deep: #d6ad2c;
    --white: #ffffff;
  }
  * { box-sizing: border-box; margin: 0; padding: 0; }
  html, body { width: 1200px; height: 418px; overflow: hidden; }
  body { background: var(--backdrop); position: relative; }

  .card {
    position: absolute;
    top: 91px;
    width: 466px;
    height: 264px;
    overflow: hidden;
    box-shadow: 0 2px 6px rgba(0,0,0,0.18);
  }
  .card--front { left: 124px; background: radial-gradient(ellipse at 45% 35%, #ffffff 40%, #e6e6e6 100%); }
  .card--back  { left: 626px; background: linear-gradient(180deg, var(--gold-light) 0%, #f0dc6a 55%, var(--gold-deep) 100%); }

  .card__bands { position: absolute; left: 0; top: 0; width: 466px; height: 264px; }

  .card__site {
    position: absolute; left: 0; right: 0;
    text-align: center;
    font-family: "Arimo", Arial, sans-serif;
    font-weight: 700;
    white-space: nowrap;
  }
  .card--front .card__site { top: 74px; font-size: 33px; color: var(--ink-dark); }
  .card--back .card__site {
    top: 86px; font-size: 35px; color: var(--white);
    text-shadow: 1px 2px 3px rgba(0,0,0,0.45);
  }

  .card__tagline { position: absolute; left: 0; right: 0; text-align: center; white-space: nowrap; }
  .card--front .card__tagline {
    top: 120px; font-family: "Source Sans 3", sans-serif; font-size: 14px; color: var(--gold-text);
  }
  .card--back .card__tagline {
    top: 138px; font-family: "Arimo", Arial, sans-serif; font-weight: 700;
    font-size: 12.4px; letter-spacing: 0.3px; color: #111;
  }

  .contact__name {
    position: absolute; left: 26px; top: 190px;
    font-family: "Source Sans 3", sans-serif; font-weight: 600; font-size: 13px; color: var(--ink-dark);
  }
  .contact__phone {
    position: absolute; left: 26px; top: 217px;
    font-family: "Source Sans 3", sans-serif; font-size: 12.5px; color: #9a7a1c;
  }
  .contact__phone strong { color: #111; font-weight: 600; font-size: 13.5px; }
  .contact__emails {
    position: absolute; right: 22px; top: 209px;
    font-family: "Source Sans 3", sans-serif; font-size: 11px; line-height: 15px;
    color: #e8e0c4; text-align: right;
  }
  .service-note {
    position: absolute; left: 23px; top: 220px;
    font-family: "Arimo", Arial, sans-serif; font-weight: 700; font-size: 12px;
    color: var(--gold); letter-spacing: 0.2px;
  }
</style>
</head>
<body>
  <section class="card card--front" aria-label="Card front">
    <svg class="card__bands" viewBox="0 0 466 264" aria-hidden="true">
      <defs>
        <linearGradient id="goldBand" x1="0" x2="1">
          <stop offset="0" stop-color="#f3e28a"/>
          <stop offset="1" stop-color="#d9b437"/>
        </linearGradient>
      </defs>
      <polygon points="0,214 222,214 202,237 0,237" fill="url(#goldBand)"/>
      <polygon points="226,208 466,208 466,245 194,245" fill="var(--band-dark)"/>
    </svg>
    <h1 class="card__site">CalmHarborDirect.net</h1>
    <p class="card__tagline">“Too Busy to Take Care of Yourself? Think again.”</p>
    <p class="contact__name">Gerald Mossvane, MD</p>
    <p class="contact__phone">General Phone: <strong>555-417-8062</strong></p>
    <p class="contact__emails">CalmHarborDirect@mailbox-example.net<br>CalmHarbor247@mailbox-example.net</p>
  </section>

  <section class="card card--back" aria-label="Card back">
    <svg class="card__bands" viewBox="0 0 466 264" aria-hidden="true">
      <defs>
        <linearGradient id="paleBand" x1="0" x2="1">
          <stop offset="0" stop-color="#e7c94a" stop-opacity="0"/>
          <stop offset="0.5" stop-color="#fbf3a6"/>
          <stop offset="1" stop-color="#fdf6b4"/>
        </linearGradient>
      </defs>
      <polygon points="250,214 466,214 466,237 266,237" fill="url(#paleBand)"/>
      <polygon points="0,208 258,208 276,245 0,245" fill="var(--band-dark)"/>
    </svg>
    <h2 class="card__site">CalmHarborDirect.net</h2>
    <p class="card__tagline">“NOT ENOUGH TIME TO CARE FOR YOURSELF”</p>
    <p class="service-note">24-HOUR ANSWERING SERVICE</p>
  </section>
</body>
</html>
```